Mastering Modern Vineyard Management

size of the ad - 8”x 10.75" plus 0.25" bleed
I would like an ad for a magazine that will stand out and make people want to read the ad.
The ad should not be crowded and people reading the ad will be able to read the text.
I would like it to be a creative and modern-day design.
the list of topics should not be the focus of the ad.
the text is attached.
If you decide to use people in the ad then please no ladies.
please note that leave over 1 inch for the bottom of the footer

```html
<!DOCTYPE html>
<html lang="en">
<head>
<meta charset="utf-8">
<title>Vineyard Course – Magazine Ad</title>
<link rel="stylesheet" href="https://fonts.googleapis.com/css2?family=Bebas+Neue&family=Poppins:wght@400;500;600;700&display=swap">
<style>
  :root {
    --page-black: #000000;
    --panel-grey: #222222;
    --accent-red: #e3262f;
    --text-white: #ffffff;
    --text-soft: #f2f2f2;
    --sky-light: #c9d3dc;
    --house-white: #e4e4e2;
    --stone-grey: #5d5f63;
    --tree-green: #4f5b4a;
  }
  * { box-sizing: border-box; margin: 0; padding: 0; }
  html, body { width: 916px; height: 1200px; overflow: hidden; background: var(--page-black); }
  .ad-page {
    position: relative;
    width: 916px;
    height: 1200px;
    background: var(--page-black);
    font-family: "Poppins", sans-serif;
    color: var(--text-white);
  }
  .content-panel {
    position: absolute;
    left: 27px; top: 27px;
    width: 862px; height: 1039px;
    background: var(--panel-grey);
    overflow: hidden;
  }
  .hero-photo {
    position: absolute;
    left: 0; top: 0;
    width: 862px; height: 470px;
    background:
      linear-gradient(180deg, rgba(34,34,34,0) 60%, rgba(34,34,34,0.85) 84%, var(--panel-grey) 100%),
      linear-gradient(90deg, var(--tree-green) 0%, var(--sky-light) 14%, var(--house-white) 35%, var(--stone-grey) 55%, var(--house-white) 72%, var(--sky-light) 88%, var(--tree-green) 100%);
  }
  .headline {
    position: absolute;
    left: 0; right: 0; top: 396px;
    text-align: center;
    font-family: "Bebas Neue", sans-serif;
    font-weight: 400;
    font-size: 98px;
    line-height: 1;
    letter-spacing: 1px;
    color: var(--text-white);
  }
  .course-name {
    position: absolute;
    left: 0; right: 0; top: 480px;
    text-align: center;
    font-weight: 700;
    font-size: 23px;
    line-height: 1;
    text-transform: uppercase;
    letter-spacing: 0.2px;
  }
  .tagline-band {
    position: absolute;
    left: 108px; top: 515px;
    width: 646px; height: 30px;
    border-radius: 6px;
    background: var(--accent-red);
    font-weight: 600;
    font-size: 16px;
    line-height: 30px;
    text-align: center;
    text-transform: uppercase;
  }
  .section-title {
    position: absolute;
    left: 0; right: 0;
    text-align: center;
    font-family: "Bebas Neue", sans-serif;
    font-weight: 400;
    font-size: 58px;
    line-height: 1;
    color: var(--accent-red);
  }
  .title-location { top: 558px; }
  .title-offer { top: 696px; }
  .title-topics { top: 792px; }
  .session-details {
    position: absolute;
    left: 0; right: 0; top: 614px;
    text-align: center;
    font-size: 17px;
    line-height: 24.5px;
    color: var(--text-soft);
  }
  .offer-note {
    position: absolute;
    left: 0; right: 0; top: 754px;
    text-align: center;
    font-size: 17px;
    line-height: 24px;
    color: var(--text-soft);
  }
  .topic-list {
    position: absolute;
    top: 858px;
    width: 380px;
    list-style: none;
    text-align: center;
    font-size: 17px;
    line-height: 35.2px;
    color: var(--text-soft);
  }
  .topic-list-left { left: 48px; }
  .topic-list-right { left: 420px; }
  .topic-divider {
    position: absolute;
    left: 402px; top: 858px;
    width: 2px; height: 170px;
    background: linear-gradient(180deg, rgba(227,38,47,0) 0%, var(--accent-red) 50%, rgba(227,38,47,0) 100%);
  }
  .footer-margin-note {
    position: absolute;
    left: 0; right: 0; top: 1088px;
    display: flex;
    flex-direction: column;
    align-items: center;
    gap: 2px;
    font-weight: 600;
    font-size: 11px;
    line-height: 14px;
  }
</style>
</head>
<body>
<main class="ad-page">
  <section class="content-panel">
    <div class="hero-photo" role="img" aria-label="Photograph of a modern two-storey white house with stone pillars, large windows and a dark garage door, surrounded by trees"></div>

    <h1 class="headline">Vineyard Course</h1>
    <h2 class="course-name">Mastering Modern Vineyard Management</h2>
    <p class="tagline-band">Investing in knowledge is investing in opportunities.</p>

    <h3 class="section-title title-location">Millbrook</h3>
    <p class="session-details">10 -Tuesday evenings sessions<br>Starting Feb.28<br>Limited Partial Scholarships</p>

    <h3 class="section-title title-offer">Early Bird Special</h3>
    <p class="offer-note">For those that started or would like to go into vineyard management</p>

    <h3 class="section-title title-topics">Topics: Partial Listing</h3>
    <ul class="topic-list topic-list-left">
      <li>Financing</li>
      <li>Grape varieties</li>
      <li>Soil and climate</li>
      <li>Canopy management</li>
      <li>Vineyard legal basics</li>
    </ul>
    <div class="topic-divider"></div>
    <ul class="topic-list topic-list-right">
      <li>Irrigation</li>
      <li>Pest control</li>
      <li>Tax fundamentals</li>
      <li>Harvest planning</li>
      <li>Vineyard investment strategies</li>
    </ul>
  </section>

  <div class="footer-margin-note">
    <svg width="8" height="10" viewBox="0 0 8 10" aria-hidden="true"><path d="M4 10V1M1 4l3-3 3 3" stroke="#fff" stroke-width="1.2" fill="none"/></svg>
    <span>1 Inch Free</span>
    <svg width="8" height="10" viewBox="0 0 8 10" aria-hidden="true"><path d="M4 0v9M1 6l3 3 3-3" stroke="#fff" stroke-width="1.2" fill="none"/></svg>
  </div>
</main>
</body>
</html>
```